Clear Harbor Business card

We are a company that owns 2 compliance software programs for TV, Radio and Cable industries as well as an online job board. We need a professional business card that incorproates all three logos.

```html
<!DOCTYPE html>
<html lang="en">
<head>
<meta charset="utf-8">
<title>Clear Harbor Business Card</title>
<link href="https://fonts.googleapis.com/css2?family=Montserrat:wght@400;600;700&display=swap" rel="stylesheet">
<style>
  :root{
    --navy:#2c2a6f;
    --white:#ffffff;
    --orange:#e8452c;
    --blue:#2a7fc4;
    --stage:#2a2b2f;
    --ink-soft:#e8e8f4;
  }
  *{box-sizing:border-box;margin:0;padding:0}
  html,body{width:1200px;height:800px;overflow:hidden}
  body{background:var(--stage);font-family:"Montserrat",Arial,sans-serif;position:relative}
  .card{position:absolute;left:320px;width:560px;height:320px;box-shadow:0 10px 30px rgba(0,0,0,.45);overflow:hidden}
  .card--front{top:50px;background:var(--white);display:flex;align-items:center;justify-content:center}
  .card--back{top:430px;background:var(--navy);display:flex}

  .brand-row{display:flex;align-items:center}
  .brand{display:flex;align-items:center;gap:7px;color:var(--navy);font-weight:700;font-size:15px;line-height:1.1;padding:0 16px}
  .brand__dot{width:11px;height:11px;border-radius:50%;background:var(--orange);flex:none}
  .brand__dot--blue{background:var(--blue)}
  .brand-divider{width:1.5px;height:62px;background:var(--navy)}

  .back__brands{width:150px;background:var(--white);display:flex;flex-direction:column;justify-content:center;align-items:flex-start;padding-left:6px}
  .back__brands .brand{font-size:12px;padding:12px 8px}
  .back__brands .brand-divider{width:70px;height:1.5px;margin-left:14px}

  .back__info{flex:1;position:relative;color:var(--white)}
  .person{position:absolute;left:34px;top:116px}
  .person__name{font-weight:700;font-size:21px}
  .person__role{font-weight:400;font-size:12px;margin-top:2px}
  .info-rule{position:absolute;left:34px;right:28px;top:170px;height:1.5px;background:var(--white)}
  .address{position:absolute;right:28px;top:92px;text-align:right;font-size:12px;line-height:1.55}
  .contacts{position:absolute;left:34px;top:186px;list-style:none;font-size:12px}
  .contacts li{display:flex;align-items:center;gap:8px;margin-bottom:7px}
  .contacts svg{width:16px;height:16px;flex:none}
</style>
</head>
<body>
  <section class="card card--front" aria-label="Card front">
    <div class="brand-row">
      <div class="brand"><span class="brand__dot"></span>Clear Harbor<br>Broadcast</div>
      <div class="brand-divider"></div>
      <div class="brand"><span class="brand__dot"></span>Clear Harbor<br>Cable</div>
      <div class="brand-divider"></div>
      <div class="brand"><span class="brand__dot brand__dot--blue"></span>CrewPost<br>Jobs</div>
    </div>
  </section>

  <section class="card card--back" aria-label="Card back">
    <div class="back__brands">
      <div class="brand"><span class="brand__dot brand__dot--blue"></span>CrewPost Jobs</div>
      <div class="brand-divider"></div>
      <div class="brand"><span class="brand__dot"></span>Clear Harbor Cable</div>
      <div class="brand-divider"></div>
      <div class="brand"><span class="brand__dot"></span>Clear Harbor Broadcast</div>
    </div>
    <div class="back__info">
      <div class="address">PO BOX 123<br>Street Address<br>2nd Lane, Arizona</div>
      <div class="person">
        <p class="person__name">Dana Whitfield</p>
        <p class="person__role">Owner</p>
      </div>
      <div class="info-rule"></div>
      <ul class="contacts">
        <li>
          <svg viewBox="0 0 16 16" aria-hidden="true"><circle cx="8" cy="8" r="7.5" fill="#fff"/><path d="M5.4 4.2l1.3 1.6-.7 1a5 5 0 0 0 2.9 2.9l1-.7 1.6 1.3-.7 1.3c-3.2-.2-6.4-3.4-6.6-6.6z" fill="#2c2a6f"/></svg>
          555.555.5555
        </li>
        <li>
          <svg viewBox="0 0 16 16" aria-hidden="true"><circle cx="8" cy="8" r="7.5" fill="#fff"/><rect x="4" y="5.3" width="8" height="5.6" fill="none" stroke="#2c2a6f" stroke-width="1.1"/><path d="M4 5.5l4 3 4-3" fill="none" stroke="#2c2a6f" stroke-width="1.1"/></svg>
          info@clearharbormail.com
        </li>
        <li>
          <svg viewBox="0 0 16 16" aria-hidden="true"><circle cx="8" cy="8" r="7.5" fill="#fff"/><circle cx="8" cy="8" r="4" fill="none" stroke="#2c2a6f" stroke-width="1"/><ellipse cx="8" cy="8" rx="1.8" ry="4" fill="none" stroke="#2c2a6f" stroke-width="1"/><path d="M4 8h8" stroke="#2c2a6f" stroke-width="1"/></svg>
          www.clearharborweb.com
        </li>
      </ul>
    </div>
  </section>
</body>
</html>
```